KLV Plant Services

We are a heavy diesel mechanical business with additional air con certificates, remapping engine rebuilt

Contact Information for Business Card

Company Name, Director Name, Managing Director, Contact details, email and website

Font styles to use
Serif
Script

```html
<!DOCTYPE html>
<html lang="en">
<head>
<meta charset="UTF-8">
<title>KLV Plant Services – Business Card</title>
<link href="https://fonts.googleapis.com/css2?family=Poppins:wght@400;500;700;800&display=swap" rel="stylesheet">
<style>
  :root {
    --navy: #0c0b86;
    --navy-deep: #08076a;
    --ink: #111111;
    --paper: #ffffff;
    --stage: #e6e6e8;
  }
  * { margin: 0; padding: 0; box-sizing: border-box; }
  html, body { width: 1200px; height: 900px; overflow: hidden; }
  body {
    background: var(--stage);
    font-family: "Poppins", sans-serif;
    display: flex;
    flex-direction: column;
    align-items: center;
    justify-content: center;
    gap: 40px;
  }
  .card {
    position: relative;
    width: 700px;
    height: 400px;
    overflow: hidden;
    box-shadow: 0 6px 18px rgba(0,0,0,0.18);
  }

  /* Back side */
  .card-back { background: var(--navy); }
  .card-back .pattern-area {
    position: absolute; inset: 0;
    background: linear-gradient(135deg, var(--navy) 0%, var(--navy-deep) 100%);
  }
  .card-back .back-name {
    position: absolute;
    right: 34px;
    top: 150px;
    color: var(--paper);
    font-weight: 700;
    font-size: 13px;
    display: flex;
    align-items: center;
    gap: 6px;
  }
  .back-name .dot {
    width: 10px; height: 10px; border-radius: 50%; background: var(--paper);
  }

  /* Front side */
  .card-front { background: var(--paper); }
  .brand-name {
    position: absolute;
    left: 40px;
    top: 118px;
    width: 290px;
    color: var(--navy);
    font-weight: 800;
    line-height: 1;
    display: flex;
    align-items: center;
    gap: 14px;
  }
  .brand-name .mark-circle {
    flex: none;
    width: 22px; height: 22px; border-radius: 50%; background: var(--navy);
  }
  .brand-name .brand-text { font-size: 34px; }
  .brand-name .brand-text span { display: block; font-size: 24px; margin-top: 6px; }

  .divider {
    position: absolute;
    left: 362px; top: 90px;
    width: 3px; height: 185px;
    background: var(--navy);
  }
  .details {
    position: absolute;
    left: 388px; top: 96px;
    color: var(--ink);
  }
  .person-name {
    color: var(--navy);
    font-weight: 800;
    font-size: 27px;
    letter-spacing: 0.5px;
    line-height: 1.05;
  }
  .person-role { font-size: 14px; margin-bottom: 18px; }
  .address { font-size: 15px; line-height: 1.3; margin-bottom: 14px; }
  .contact-list { list-style: none; font-size: 16px; line-height: 1.35; }
  .contact-list li { display: flex; align-items: center; gap: 8px; }
  .contact-list svg { width: 13px; height: 13px; flex: none; }
  .web-domain { color: var(--navy); }

  .footer-wave { position: absolute; left: 0; bottom: 0; width: 700px; height: 120px; }
</style>
</head>
<body>

  <section class="card card-back" aria-label="Business card back">
    <div class="pattern-area" role="img" aria-label="Repeating embossed brand pattern in dark navy"></div>
    <div class="back-name"><i class="dot"></i>KLV Plant Services</div>
  </section>

  <section class="card card-front" aria-label="Business card front">
    <div class="brand-name">
      <i class="mark-circle"></i>
      <div class="brand-text">KLV<span>Plant Services</span></div>
    </div>

    <div class="divider"></div>

    <div class="details">
      <h1 class="person-name">MARK DELANEY</h1>
      <p class="person-role">Director</p>
      <p class="address">2270 Harlow Ridge Rd Stonebrook,<br>GA 30418</p>
      <ul class="contact-list">
        <li>
          <svg viewBox="0 0 24 24"><path fill="#0c0b86" d="M6.6 10.8a15 15 0 0 0 6.6 6.6l2.2-2.2a1 1 0 0 1 1-.25 11.4 11.4 0 0 0 3.6.57 1 1 0 0 1 1 1V20a1 1 0 0 1-1 1A17 17 0 0 1 3 4a1 1 0 0 1 1-1h3.5a1 1 0 0 1 1 1c0 1.25.2 2.45.57 3.57a1 1 0 0 1-.25 1z"/></svg>
          470-555-0182
        </li>
        <li>
          <svg viewBox="0 0 24 24"><rect x="2.5" y="5" width="19" height="14" rx="1.5" fill="none" stroke="#0c0b86" stroke-width="2.2"/><path d="M3 6l9 7 9-7" fill="none" stroke="#0c0b86" stroke-width="2.2"/></svg>
          info@klvplantservices.com
        </li>
        <li>
          <svg viewBox="0 0 24 24"><circle cx="12" cy="12" r="9.5" fill="none" stroke="#0c0b86" stroke-width="2.2"/><path d="M2.5 12h19M12 2.5c3 3 3 16 0 19M12 2.5c-3 3-3 16 0 19" fill="none" stroke="#0c0b86" stroke-width="1.8"/></svg>
          www.<span class="web-domain">klvplantservices</span>.com
        </li>
      </ul>
    </div>

    <svg class="footer-wave" viewBox="0 0 700 120" preserveAspectRatio="none">
      <path d="M0 12 C200 10 380 95 700 82 L700 88 C380 102 200 22 0 22 Z" fill="var(--ink)"/>
      <path d="M0 36 C220 34 400 110 700 98 L700 120 L0 120 Z" fill="var(--navy)"/>
    </svg>
  </section>

</body>
</html>
```